Brightwave Reach - Business Card

We need a business card for a Social Media Marketing company that specializes in online marketing for small businesses in Canada using common Social Media platforms such as Pixlora, Chatterly, Blinkpost & Quibber.

I have uploaded a copy of our logo which I would like utilized in the business card. We would like the business card to be modern yet classy design.

Our website is www.brightwavereach.ca

Industry/Entity Type

Marketing

Contact Information for Business Card

Email: info@brightwavereach.ca
Website: www.brightwavereach.ca
Telephone: 604-555-0193

Colors

Designer to choose colors to be used in the design.

Requirements
Must have
• Social Media icons on reverse
• Please add some designs with color.

```html
<!DOCTYPE html>
<html lang="en">
<head>
<meta charset="utf-8">
<title>Brightwave Reach – Business Card</title>
<link rel="stylesheet" href="https://fonts.googleapis.com/css2?family=Open+Sans:wght@400;600;800&display=swap">
<style>
  :root {
    --stage: #000000;
    --card-light: #f2f2f2;
    --card-dark: #3d4244;
    --ink: #4f5254;
    --ink-soft: #5e6163;
    --mark-light: #47494b;
    --mark-dark: #f1f1f1;
  }
  * { margin: 0; padding: 0; box-sizing: border-box; }
  html, body {
    width: 1200px; height: 900px; overflow: hidden;
    background: var(--stage);
    font-family: "Open Sans", Arial, sans-serif;
  }
  .stage { position: relative; width: 1200px; height: 900px; }
  .card { position: absolute; top: 200px; width: 309px; height: 501px; }
  .card--front {
    left: 293px; background: var(--card-light);
    border-radius: 62px 0 62px 0;
  }
  .card--back {
    left: 613px; background: var(--card-dark);
    border-radius: 0 62px 0 62px;
  }
  .brand {
    position: absolute; display: flex; flex-direction: column; align-items: center;
    font-weight: 800; text-transform: uppercase; line-height: 1.05; text-align: center;
    letter-spacing: 0.5px;
  }
  .brand__square { width: 14px; height: 14px; margin-bottom: 10px; }
  .card--front .brand { left: 0; width: 309px; top: 78px; font-size: 30px; color: var(--mark-light); }
  .card--front .brand__square { background: var(--mark-light); }
  .card--back .brand { left: 0; width: 309px; top: 334px; font-size: 33px; color: var(--mark-dark); }
  .card--back .brand__square { background: var(--mark-dark); }
  .person { position: absolute; left: 22px; top: 336px; }
  .person__name { font-size: 16px; font-weight: 600; color: var(--ink); }
  .person__role { font-size: 13px; color: var(--ink-soft); margin-top: 1px; }
  .contacts { position: absolute; left: 24px; top: 410px; list-style: none; }
  .contacts li {
    display: flex; align-items: center; gap: 6px;
    font-size: 13px; color: var(--ink-soft); height: 18px;
  }
  .contacts svg { width: 10px; height: 10px; fill: var(--ink); }
</style>
</head>
<body>
<main class="stage">
  <section class="card card--front">
    <div class="brand">
      <span class="brand__square"></span>
      <span>Brightwave</span>
      <span>Reach</span>
    </div>
    <div class="person">
      <p class="person__name">Daniel Marsh</p>
      <p class="person__role">Managing Director</p>
    </div>
    <ul class="contacts">
      <li>
        <svg viewBox="0 0 10 10" aria-hidden="true"><path d="M1 3.5C1 2 2 1.5 5 1.5S9 2 9 3.5L7.5 4 7 3H3L2.5 4ZM2.5 5H7.5L8.5 8.5H1.5Z"/></svg>
        604-555-0193
      </li>
      <li>
        <svg viewBox="0 0 10 10" aria-hidden="true"><path d="M1 2.5H9V8H1Z M1.5 3L5 5.5 8.5 3" stroke="#f2f2f2" stroke-width="0.8"/></svg>
        info@brightwavereach.ca
      </li>
      <li>
        <svg viewBox="0 0 10 10" aria-hidden="true"><circle cx="5" cy="5" r="4.3"/><path d="M3 3.5 5 4 4.5 6 3 5.5Z M6 5.5 7.5 5 7 7.5Z" fill="#f2f2f2"/></svg>
        www.brightwavereach.ca
      </li>
    </ul>
  </section>

  <section class="card card--back">
    <div class="brand">
      <span class="brand__square"></span>
      <span>Brightwave</span>
      <span>Reach</span>
    </div>
  </section>
</main>
</body>
</html>
```